KTR Photography Editing & Support Services for Real Estate

We require a double sided A4 flyer to promote our photography services to real estate agencies.
This particular service is targeted to rural areas where reliable, professional and highly skilled photographers are difficult to source. We teach the agent how to photograph, they upload files to a server and we take care of the rest (image editing, quality control and delivery). This will give the agents flexibility with when to shoot and eliminates the stress of managing a photographer / contractor. We offer a 1 day face to face training session and competitive packages for equipment start up.
We would like the flyer to look clean & very professional. The flyer should showcase samples of our work to highlight what can be achieved by using our services. We like the look of a black or dark background behind the text and feel that would look nice with our photographs provided. Otherwise open to your suggestions and ideas.
TEXT FOR FLYER:
Welcome to the KTR Real Estate Photography Editing and Support Service
• Take your real estate business to the next level by providing impressive real estate imagery that makes you stands out from the competition
• Omit the stress of trying to find a good photographer or managing an unreliable one and hence have more time to focus on other aspects of your business
• Showcase your listings with better quality and more impactful photographs than your competitors thereby increasing potential for a quick sale
• Great first impressions matter and you will achieve this by looking and feeling more professional. This will attract and retain more future clients.
HOW IT WORKS
• We understand that your time is valuable, so let us handle the editing and delivery of your images. You shoot, and we take care of the rest.
• Images are edited and delivered within 1 working day
INCLUSIONS:
• Full day face to face training (we come to you) and instructional handbook
• We will teach you everything you need to know about your equipment and how to take stunning real estate photographs
• Service turnaround within 1 working day
• Free HELP desk service Mon-Fri
• 12 month Exclusivity (rural towns only) for a limited time
INVESTMENT
• 99 per listing for us to manage images including editing, quality control and delivery (10 Images)
• Ask us about competitive packages for photography equipment if required
SUMMARY
The KTR Real Estate Photography Editing and Support Service is the perfect solution for busy real estate professionals who want to take their business to the next level. Our service is affordable, flexible, and designed to help you showcase your listings in the best possible light.
Contact us today to learn more about how we can help you.

```html
<!DOCTYPE html>
<html lang="en">
<head>
<meta charset="utf-8">
<title>KTR Real Estate Photography Editing Flyer</title>
<link rel="stylesheet" href="https://fonts.googleapis.com/css2?family=Montserrat:wght@300;400;500;800;900&family=Poppins:wght@400;500&family=Libre+Bodoni:wght@700&display=swap">
<style>
:root{
  --gold:#b07a22;
  --black:#111111;
  --ink:#1a1a1a;
  --panel:#e9e9e9;
  --canvas:#efefef;
  --white:#ffffff;
  --muted:#d6d6d6;
}
*{box-sizing:border-box;margin:0;padding:0}
html,body{width:1200px;height:2809px;overflow:hidden}
body{background:var(--canvas);font-family:"Poppins",sans-serif;position:relative}
.page{position:absolute;left:130px;width:940px;height:1330px;background:var(--black);overflow:hidden;box-shadow:0 6px 18px rgba(0,0,0,.18)}
.page--front{top:50px}
.page--back{top:1430px}

/* front hero */
.hero{position:absolute;left:0;top:0;width:940px;height:990px;
  background:linear-gradient(180deg,#a7b8d4 0%,#bcc3d6 22%,#d9bdb7 38%,#8f98a6 46%,#4e5b5a 55%,#2d3528 66%,#151515 82%,#111 100%)}
.hero__cabin{position:absolute;left:0;top:100px;width:290px;height:330px;background:linear-gradient(90deg,#2a2a2c,#3a3a3d);opacity:.9}
.brand{position:absolute;right:60px;top:150px;text-align:center;width:430px}
.brand__name{font-family:"Montserrat",sans-serif;font-weight:300;font-size:36px;letter-spacing:8px;color:#444;text-transform:uppercase}
.welcome{position:absolute;left:54px;top:540px}
.welcome__title{font-family:"Montserrat",sans-serif;font-weight:900;font-size:50px;color:var(--white);letter-spacing:1px}
.welcome__sub{font-family:"Libre Bodoni",serif;font-weight:700;font-size:31px;line-height:1.35;color:var(--gold);text-transform:uppercase;margin-top:6px}
.welcome__rule{width:68px;height:4px;background:var(--white);margin-top:18px}

.points{position:absolute;left:54px;width:840px;display:grid;grid-template-columns:1fr 1fr;column-gap:40px;row-gap:34px}
.point{display:flex;gap:14px;font-size:12.5px;line-height:1.35;color:var(--muted);max-width:380px}
.point svg{flex:none;width:24px;height:24px;margin-top:1px}
.front-points{top:758px}

.strip__band{position:absolute;left:0;width:940px;background:var(--gold)}
.shot{position:absolute;border:3px solid var(--white)}

/* contact bar */
.cta{position:absolute;left:0;top:1164px;width:940px;height:59px;display:flex;font-family:"Montserrat",sans-serif;font-size:25px;font-weight:500}
.cta__lead{background:var(--black);color:var(--white);width:295px;display:flex;align-items:center;padding-left:54px;position:relative}
.cta__lead::after{content:"";position:absolute;right:-16px;top:21px;border-left:16px solid var(--black);border-top:9px solid transparent;border-bottom:9px solid transparent}
.cta__rest{background:var(--gold);color:var(--black);flex:1;display:flex;align-items:center;padding-left:34px}

.footer{position:absolute;left:0;bottom:0;width:940px;height:111px;background:var(--panel);display:flex;align-items:center;padding-left:54px;gap:18px;color:var(--ink);font-size:14px}
.footer__phone{font-family:"Montserrat",sans-serif;font-size:28px;font-weight:500;display:flex;align-items:center;gap:12px}
.footer__item{display:flex;align-items:center;gap:9px}
.footer__sep{font-size:34px;font-weight:300;color:#333}
.footer svg{flex:none}

/* back */
.back-top{position:absolute;left:0;top:0;width:940px;height:98px;background:var(--gold)}
.section{position:absolute;width:420px}
.section__head{display:flex;align-items:center;gap:16px;font-family:"Montserrat",sans-serif;font-weight:500;font-size:27px;color:var(--gold);text-transform:uppercase;margin-bottom:24px}
.section__head svg{flex:none}
.section .point{margin-bottom:14px}
.lounge{position:absolute;left:0;top:740px;width:940px;height:350px;background:radial-gradient(ellipse at 55% 65%,#3a3a3c 0%,#222224 45%,#121212 80%)}
.summary{position:absolute;left:0;top:1088px;width:940px;height:131px;background:var(--gold);padding:34px 54px 0;font-size:15.5px;line-height:1.4;color:var(--black)}
</style>
</head>
<body>

<svg width="0" height="0" style="position:absolute">
  <defs>
    <symbol id="tick" viewBox="0 0 24 24"><circle cx="12" cy="12" r="10" fill="none" stroke="#b07a22" stroke-width="1.6"/><path d="M7 12.3l3.3 3.3L17.5 8" fill="none" stroke="#b07a22" stroke-width="2" stroke-linecap="round" stroke-linejoin="round"/></symbol>
    <symbol id="phone" viewBox="0 0 24 24"><path d="M6.6 2.5l3 3.2-1.8 2.4c1.2 2.6 3.4 4.8 6 6l2.4-1.8 3.3 3-1.6 3.2C11 18.5 5.5 13 3.4 4.1z" fill="none" stroke="#b07a22" stroke-width="2" stroke-linejoin="round"/></symbol>
    <symbol id="globe" viewBox="0 0 24 24"><circle cx="12" cy="12" r="10" fill="#b07a22"/><path d="M2 12h20M12 2c3 3 3 17 0 20M12 2c-3 3-3 17 0 20" stroke="#e9e9e9" stroke-width="1.3" fill="none"/></symbol>
    <symbol id="mail" viewBox="0 0 24 18"><rect x="1" y="1" width="22" height="16" rx="1.5" fill="#b07a22"/><path d="M2 2l10 8 10-8" stroke="#e9e9e9" stroke-width="1.6" fill="none"/></symbol>
  </defs>
</svg>

<!-- FRONT -->
<section class="page page--front">
  <div class="hero" role="img" aria-label="Clifftop dark timber cabin overlooking the ocean at dusk">
    <div class="hero__cabin"></div>
  </div>

  <div class="brand"><p class="brand__name">Owen Hartley</p></div>

  <div class="welcome">
    <h1 class="welcome__title">WELCOME TO THE</h1>
    <p class="welcome__sub">KTR Real Estate Photography Editing<br>and Support Service</p>
    <div class="welcome__rule"></div>
  </div>

  <div class="points front-points">
    <p class="point"><svg><use href="#tick"/></svg><span>Take your real estate business to the next level by providing impressive real estate imagery that makes you stands out from the competition</span></p>
    <p class="point"><svg><use href="#tick"/></svg><span>Showcase your listings with better quality and more impactful photographs than your competitors thereby increasing potential for a quick sale</span></p>
    <p class="point"><svg><use href="#tick"/></svg><span>Omit the stress of trying to find a good photographer or managing an unreliable one and hence have more time to focus on other aspects of your business</span></p>
    <p class="point"><svg><use href="#tick"/></svg><span>Great first impressions matter and you will achieve this by looking and feeling more professional. This will attract and retain more future clients.</span></p>
  </div>

  <div class="strip__band" style="top:1066px;height:98px"></div>
  <div class="shot" style="left:54px;top:968px;width:268px;height:185px;background:linear-gradient(160deg,#1d2b3d,#6a6f78 45%,#8a6a48 80%,#3a2b1f)" role="img" aria-label="Living room with floor-to-ceiling windows at dusk"></div>
  <div class="shot" style="left:340px;top:968px;width:266px;height:185px;background:linear-gradient(150deg,#d8d8d6,#b7b3aa 50%,#7d6f5e)" role="img" aria-label="Bright hallway with artwork and timber console"></div>
  <div class="shot" style="left:620px;top:968px;width:266px;height:185px;background:linear-gradient(180deg,#8fa4c4,#c7cad3 40%,#9a8a78 70%,#4a4438)" role="img" aria-label="Gabled farmhouse exterior lit at twilight"></div>

  <div class="cta">
    <div class="cta__lead">Contact us today</div>
    <div class="cta__rest">to learn more about how we can help you</div>
  </div>

  <footer class="footer">
    <span class="footer__phone"><svg width="26" height="26"><use href="#phone"/></svg>1234567890</span>
    <span class="footer__sep">|</span>
    <span class="footer__item"><svg width="17" height="17"><use href="#globe"/></svg>www.ktrphotoediting.com</span>
    <span class="footer__sep">|</span>
    <span class="footer__item"><svg width="18" height="14"><use href="#mail"/></svg>info@ktrphotoediting.com</span>
  </footer>
</section>

<!-- BACK -->
<section class="page page--back">
  <div class="back-top"></div>
  <div class="shot" style="left:48px;top:65px;width:265px;height:185px;background:linear-gradient(170deg,#f1f0ed,#d9d3c9 55%,#a98d6a)" role="img" aria-label="Open-plan white kitchen and dining area"></div>
  <div class="shot" style="left:331px;top:65px;width:265px;height:185px;background:linear-gradient(160deg,#e9ecef,#c5cdd3 50%,#8d8f8a)" role="img" aria-label="Bedroom with large windows onto the landscape"></div>
  <div class="shot" style="left:614px;top:65px;width:265px;height:185px;background:linear-gradient(180deg,#6f8ab0,#a9b3c0 40%,#5a4f42 65%,#5e7a3c)" role="img" aria-label="Dark-clad home exterior with lawn at dusk"></div>

  <div class="section" style="left:48px;top:330px">
    <h2 class="section__head">
      <svg width="34" height="34" viewBox="0 0 34 34" fill="none" stroke="#fff" stroke-width="2"><circle cx="10" cy="6" r="3.5"/><path d="M9 11v10h8l3 9M9 16h8M4 22h26M26 22v10M4 22v10"/><rect x="18" y="11" width="10" height="7"/></svg>
      How it works</h2>
    <p class="point"><svg><use href="#tick"/></svg><span>We understand that your time is valuable, so let us handle the editing and delivery of your images. You shoot, and we take care of the rest.</span></p>
    <p class="point"><svg><use href="#tick"/></svg><span>Images are edited and delivered within 1 working day</span></p>
  </div>

  <div class="section" style="left:48px;top:610px">
    <h2 class="section__head">
      <svg width="34" height="34" viewBox="0 0 34 34" fill="none" stroke="#fff" stroke-width="2"><path d="M12 4h10l-3 6h-4z"/><path d="M15 10c-6 3-9 9-9 14 0 4 3 6 11 6s11-2 11-6c0-5-3-11-9-14"/><path d="M17 15v10M20 17h-4a2 2 0 000 4h2a2 2 0 010 4h-4"/></svg>
      Investment</h2>
    <p class="point"><svg><use href="#tick"/></svg><span>99 per listing for us to manage images including editing, quality control and delivery (10 Images)</span></p>
  </div>

  <div class="section" style="left:494px;top:330px">
    <h2 class="section__head">
      <svg width="34" height="34" viewBox="0 0 34 34" fill="none" stroke="#fff" stroke-width="2"><rect x="3" y="8" width="28" height="21" rx="2"/><circle cx="17" cy="18.5" r="6"/><circle cx="17" cy="18.5" r="2.5"/><path d="M11 8l2-4h8l2 4"/></svg>
      Inclusions</h2>
    <p class="point"><svg><use href="#tick"/></svg><span>Full day face to face training (we come to you) and instructional handbook</span></p>
    <p class="point"><svg><use href="#tick"/></svg><span>We will teach you everything you need to know about your equipment and how to take stunning real estate photographs</span></p>
    <p class="point"><svg><use href="#tick"/></svg><span>Service turnaround within 1 working day</span></p>
    <p class="point"><svg><use href="#tick"/></svg><span>Free HELP desk service Mon-Fri</span></p>
    <p class="point"><svg><use href="#tick"/></svg><span>12 month Exclusivity (rural towns only) for a limited time</span></p>
  </div>

  <div class="section" style="left:494px;top:668px">
    <p class="point"><svg><use href="#tick"/></svg><span>Ask us about competitive packages for photography equipment if required</span></p>
  </div>

  <div class="lounge" role="img" aria-label="Dimly lit lounge with dark sofa, cushions and side table"></div>

  <p class="summary">The KTR Real Estate Photography Editing and Support Service is the perfect solution for busy real estate professionals who want to take their business to the next level. Our service is affordable, flexible, and designed to help you showcase your listings in the best possible light.</p>

  <footer class="footer">
    <span class="footer__phone"><svg width="26" height="26"><use href="#phone"/></svg>1234567890</span>
    <span class="footer__item" style="margin-left:40px"><svg width="17" height="17"><use href="#globe"/></svg>www.ktrphotoediting.com</span>
    <span class="footer__item" style="margin-left:30px"><svg width="18" height="14"><use href="#mail"/></svg>info@ktrphotoediting.com</span>
  </footer>
</section>

</body>
</html>
```